Investment Management Firm Power point template

Marrow Holdings is a real estate investment firm focused on buying commercial office and residential property in the UK. We produce powerpoint presentations for our Board of Directors, Investment Committee and also to external investors.

We are looking for a powerpoint design template which we can use for future presentations which provide a professional look and feel.

Our current website: http://www.marrowholdings.example.co.uk/

Target Market(s)

Institution Investors, Board of Directors, Professionals

Industry/Entity Type

Real Estate

Requirements
Must have
• Leverage off the current logo and colour scheme. However, does not have to purely rely on this colour scheme.
• - Title page
• - Content Page
• - Slide where graphs can be incorporated
• - Slide where photos can be incorporated
• - Slide of UK Map which can show where the property portfolio is currently located
• - Other slides incorporating smart art or other designs that can be used for future presentations
Nice to have
• An example of graphics that we would love to have in the powerpoint pack which we can easily edit has been attached

```html
<!DOCTYPE html>
<html lang="en">
<head>
<meta charset="utf-8">
<title>Marrow Holdings – Content Slide</title>
<link rel="stylesheet" href="https://fonts.googleapis.com/css2?family=Fira+Sans:wght@400;500;600;700&display=swap">
<style>
  :root {
    --navy: #15497f;
    --heading-blue: #2f6897;
    --band-blue: #286893;
    --body-text: #2b2b2b;
    --frame-blue: #5f8fb4;
    --white: #ffffff;
  }
  * { margin: 0; padding: 0; box-sizing: border-box; }
  html, body {
    width: 1200px;
    height: 900px;
    overflow: hidden;
    background: var(--white);
  }
  .slide {
    position: relative;
    width: 1200px;
    height: 900px;
    background: var(--white);
    font-family: "Fira Sans", Arial, sans-serif;
    overflow: hidden;
  }
  .slide-title {
    position: absolute;
    left: 36px;
    top: 28px;
    font-size: 36px;
    font-weight: 700;
    color: var(--navy);
    letter-spacing: -0.2px;
  }
  .title-rule {
    position: absolute;
    left: 0;
    top: 71px;
    width: 290px;
    height: 3px;
    background: var(--navy);
  }
  .content-column {
    position: absolute;
    top: 170px;
    width: 500px;
  }
  .content-column.left { left: 66px; }
  .content-column.right { left: 652px; }
  .column-heading {
    font-size: 27px;
    font-weight: 600;
    color: var(--heading-blue);
    line-height: 1.2;
    margin-bottom: 12px;
  }
  .column-body {
    padding-left: 4px;
    font-size: 19px;
    line-height: 33px;
    color: var(--body-text);
  }
  .column-body p + p { margin-top: 33px; }
  .footer-band {
    position: absolute;
    left: 0;
    bottom: 0;
    width: 912px;
    height: 57px;
    background: var(--band-blue);
  }
  .footer-brand {
    position: absolute;
    left: 920px;
    top: 843px;
    width: 273px;
    height: 51px;
    border: 1.5px solid var(--frame-blue);
    display: flex;
    align-items: center;
    justify-content: center;
    gap: 12px;
  }
  .brand-square {
    width: 18px;
    height: 18px;
    background: var(--navy);
  }
  .brand-name {
    font-size: 26px;
    font-weight: 500;
    color: var(--navy);
    letter-spacing: -0.3px;
  }
</style>
</head>
<body>
<main class="slide">
  <h1 class="slide-title">Slide Title Here</h1>
  <div class="title-rule"></div>

  <section class="content-column left">
    <h2 class="column-heading">Content Paragraph Title</h2>
    <div class="column-body">
      <p>While a property’s fundamentals are important to us,<br>we put equal focus on the people who use and enjoy<br>our spaces. The experience of being in our buildings<br>— from design to atmosphere — is strategically<br>planned. Functionality and efficiency are crucial and<br>technology is in our DNA.</p>
      <p>With these fundamental characteristics in mind we<br>strive to create businesses around our properties,<br>enhancing their value and creating long-term<br>operating platforms.</p>
      <p>As part of the Harrowgate Crest Group we directly<br>and indirectly benefit from the ecosystem of<br>companies around us. Harrowgate Crest brings<br>unrivalled expertise in building successful,<br>long-lasting businesses.</p>
    </div>
  </section>

  <section class="content-column right">
    <h2 class="column-heading">Content Paragraph Title</h2>
    <div class="column-body">
      <p>While a property’s fundamentals are important to us,<br>we put equal focus on the people who use and enjoy<br>our spaces. The experience of being in our buildings<br>— from design to atmosphere — is strategically<br>planned. Functionality and efficiency are crucial and<br>technology is in our DNA.</p>
      <p>With these fundamental characteristics in mind we<br>strive to create businesses around our properties,<br>enhancing their value and creating long-term<br>operating platforms.</p>
      <p>As part of the Harrowgate Crest Group we directly<br>and indirectly benefit from the ecosystem of<br>companies around us. Harrowgate Crest brings<br>unrivalled expertise in building successful,<br>long-lasting businesses.</p>
    </div>
  </section>

  <footer>
    <div class="footer-band"></div>
    <div class="footer-brand">
      <span class="brand-square"></span>
      <span class="brand-name">Marrow Holdings</span>
    </div>
  </footer>
</main>
</body>
</html>
```